KTR Design Business Card

I need to develop a business card for my real estate design and investment company. Something clean, classic and professional with a modern vibe.

Industry/Entity Type

Real Estate

Font styles to use
Serif
Sans Serif

```html
<!DOCTYPE html>
<html lang="en">
<head>
<meta charset="utf-8">
<title>KTR Design Business Card</title>
<link rel="stylesheet" href="https://fonts.googleapis.com/css2?family=Exo+2:wght@400;500&display=swap">
<style>
  :root {
    --page: #d8d5d1;
    --card-light: #f3f3f2;
    --card-mid: #e2e2e0;
    --ink: #2f2f31;
    --ink-soft: #3c3c3e;
    --band: #3a3a3b;
    --silver: #a8a8ac;
    --silver-light: #dcdcde;
    --on-band: #f2f2f2;
  }
  html, body {
    margin: 0;
    width: 1200px;
    height: 768px;
    overflow: hidden;
    background: var(--page);
  }
  .business-card {
    position: absolute;
    left: 80px;
    top: 83px;
    width: 1040px;
    height: 602px;
    overflow: hidden;
    background: linear-gradient(100deg, var(--card-light) 0%, var(--card-mid) 55%, var(--card-light) 100%);
    box-shadow: 0 10px 30px rgba(0,0,0,0.18);
    font-family: "Exo 2", sans-serif;
  }
  .wave-area {
    position: absolute;
    left: 0;
    right: 0;
    top: 300px;
    bottom: 0;
    background: linear-gradient(100deg, var(--silver-light) 0%, var(--silver) 35%, var(--band) 62%, var(--band) 100%);
  }
  .brand-name {
    position: absolute;
    left: 58px;
    top: 140px;
    margin: 0;
    font-size: 68px;
    font-weight: 400;
    color: var(--ink-soft);
    letter-spacing: 1px;
  }
  .holder {
    position: absolute;
    right: 44px;
    top: 60px;
    text-align: right;
    color: var(--ink);
  }
  .holder-name {
    margin: 0;
    font-size: 36px;
    font-weight: 500;
    letter-spacing: 1.5px;
    line-height: 1;
  }
  .holder-title {
    margin: 12px 0 0;
    font-size: 27px;
    font-weight: 500;
    letter-spacing: 1.5px;
    line-height: 1;
  }
  .address {
    position: absolute;
    right: 44px;
    top: 336px;
    margin: 0;
    text-align: right;
    font-style: normal;
    font-size: 17px;
    line-height: 24px;
    letter-spacing: 1px;
    color: var(--on-band);
  }
  .contact-list {
    position: absolute;
    right: 40px;
    top: 416px;
    margin: 0;
    padding: 0;
    list-style: none;
    text-align: right;
    color: var(--on-band);
    letter-spacing: 1px;
  }
  .contact-list li {
    display: flex;
    justify-content: flex-end;
    align-items: center;
    gap: 9px;
    height: 35px;
    font-size: 16px;
  }
  .contact-list li.contact-online { height: 23px; font-size: 15px; }
  .contact-list svg {
    width: 17px;
    height: 17px;
    fill: none;
    stroke: var(--on-band);
    stroke-width: 1.8;
  }
</style>
</head>
<body>
  <article class="business-card">
    <div class="wave-area" role="img" aria-label="Silver and charcoal wave decoration across the lower card"></div>

    <h1 class="brand-name">KTR Design</h1>

    <header class="holder">
      <p class="holder-name">JORDAN VALCOURT</p>
      <p class="holder-title">PRESIDENT</p>
    </header>

    <address class="address">214.9th floor,Plaza<br>Harbour Lane KTR</address>

    <ul class="contact-list">
      <li>012 555 0147
        <svg viewBox="0 0 24 24"><path d="M5 3h4l2 5-3 2c1 3 3 5 6 6l2-3 5 2v4c0 1-1 2-2 2C10 21 3 14 3 5c0-1 1-2 2-2z"/></svg>
      </li>
      <li>012 555 0148
        <svg viewBox="0 0 24 24"><rect x="7" y="2" width="10" height="20" rx="2"/><path d="M11 18h2"/></svg>
      </li>
      <li>012 555 0149
        <svg viewBox="0 0 24 24"><rect x="4" y="9" width="16" height="12" rx="1"/><path d="M7 9V3h10v6M8 13h2M12 13h2M8 17h2M12 17h2"/></svg>
      </li>
      <li class="contact-online">info@ktrdesign.com
        <svg viewBox="0 0 24 24"><rect x="3" y="5" width="18" height="14"/><path d="M3 5l9 8 9-8"/></svg>
      </li>
      <li class="contact-online">www.ktrdesign.com
        <svg viewBox="0 0 24 24"><circle cx="12" cy="12" r="9"/><path d="M3 12h18M12 3c3 3 3 15 0 18M12 3c-3 3-3 15 0 18"/></svg>
      </li>
    </ul>
  </article>
</body>
</html>
```